Modern and Simple Supplement Label Design

We are looking for a Professional Graphic Designer who can design eye-catching and unique supplement label. We are supplement company who are sourcing different supplement products. I would like the design to be simple and with few colorsThe final design should communicate strength and growthI attached some samples for inspiration

Target Market(s)

Supplement Market - Collagen Supplements

Industry/Entity Type

Supplement

Font styles to use
Serif
Sans Serif

Colors

Designer to choose colors to be used in the design.

Requirements
Must have
• Front (Please search on Brindleport Collagen to get inspiration how to put together the front text)
• Logo: Vellow Naturals
• Product Name: Omni Dermal Capsules
• Hydrolyzed type I II III V & X Collagen
• Dietary Supplements - 90 capsules
• Support Joints & bones
• Rejuvenate Skin
• Promotes Healthy Hair & Nails
• One right side supplement fact and left side precaution and instruction content. ( Please find the content of the right and left side of the bottle attached)
Nice to have
• Nice to have something that shows elements bring together to create something strong or beautiful. Our brand name is Vellow Naturals. Vellow is an assembly of beams or other elements that creates a rigid structure. This is to show our supplements help to provide the elements to have strong and healthy life

```html
<!DOCTYPE html>
<html lang="en">
<head>
<meta charset="utf-8">
<title>Vellow Naturals – Omni Dermal Capsules Label</title>
<link href="https://fonts.googleapis.com/css2?family=Archivo:wght@400;500;700;800;900&family=Roboto:wght@400;500;700&display=swap" rel="stylesheet">
<style>
  :root{
    --bg:#ececec;
    --navy:#26358f;
    --red:#e3202c;
    --red-dark:#b3141d;
    --grey-text:#3b3b3b;
    --silver:#cfcfcf;
    --white:#ffffff;
  }
  *{box-sizing:border-box;margin:0;padding:0}
  html,body{width:1200px;height:917px;overflow:hidden}
  body{background:var(--bg);font-family:"Roboto",Arial,sans-serif;position:relative}

  .brand-mark{position:absolute;left:46px;top:62px;display:flex;align-items:center;gap:14px}
  .brand-mark .dot{width:34px;height:34px;border-radius:50%;background:var(--red)}
  .brand-mark .name{font-family:"Archivo",Arial,sans-serif;font-weight:700;font-size:40px;color:var(--navy);letter-spacing:.5px}

  .label{position:absolute;left:50px;top:330px;width:1100px;height:374px;background:var(--white);
    border-top:4px solid var(--silver);border-bottom:4px solid var(--silver);overflow:hidden}
  .label .band{position:absolute;left:0;right:0;top:118px;bottom:0;
    background:linear-gradient(180deg,var(--red) 0%,var(--red) 55%,var(--red-dark) 100%)}

  .info-box{position:absolute;left:14px;width:305px;background:var(--white);border:1.5px solid var(--navy);
    padding:4px 6px;font-size:10.5px;line-height:1.3;color:var(--grey-text)}
  .info-box h4{font-size:10.5px;font-weight:700;color:var(--navy)}
  .info-box.usage{top:14px;height:65px}
  .info-box.caution{top:88px;height:84px}
  .info-box.warning{top:180px;height:52px;text-align:center;font-weight:700;color:var(--navy);font-size:10.5px}
  .info-box.disclaimer{top:239px;height:52px}
  .lot-note{position:absolute;left:14px;top:342px;font-size:10.5px;color:var(--white)}

  .front{position:absolute;left:380px;top:0;width:340px;height:100%;text-align:center;font-family:"Archivo",Arial,sans-serif}
  .front .mini-brand{position:absolute;top:22px;left:0;right:0;display:flex;justify-content:center;align-items:center;gap:7px}
  .front .mini-brand .dot{width:14px;height:14px;border-radius:50%;background:var(--red)}
  .front .mini-brand .name{font-weight:700;font-size:17px;color:var(--navy)}
  .title-box{position:absolute;left:38px;top:62px;width:266px;height:62px;background:var(--white);
    border:4px solid var(--silver);padding-top:5px}
  .title-box .product{font-weight:900;font-size:27px;color:var(--navy);line-height:1;letter-spacing:-.3px}
  .title-box .form{font-weight:800;font-size:14px;color:var(--red);letter-spacing:4px;margin-top:4px}
  .type-bar{position:absolute;left:63px;top:148px;width:214px;height:24px;
    background:linear-gradient(180deg,#f4f4f4,#c9c9c9);font-weight:800;color:var(--navy);font-size:15px;letter-spacing:2px;line-height:24px}
  .collagen-bar{position:absolute;left:80px;top:172px;width:180px;height:26px;background:var(--navy);
    color:var(--white);font-weight:700;font-size:15px;line-height:26px}
  .claims{position:absolute;top:212px;left:0;right:0;list-style:none;color:var(--white);font-size:14.5px;font-weight:500}
  .claims li{padding:5px 0}
  .claims li+li{border-top:1.5px solid rgba(255,255,255,.85);margin:0 120px;padding:5px 0}
  .claims li:first-child,.claims li:last-child{margin:0}
  .claims li:nth-child(2){margin:0 135px}
  .claims li:last-child{border-top:1.5px solid rgba(255,255,255,.85);margin:0;position:relative}
  .count{position:absolute;top:304px;left:0;right:0;display:flex;justify-content:center;align-items:center;gap:6px;
    color:var(--white);font-weight:800;font-size:15px;letter-spacing:1px}
  .count .num{width:24px;height:24px;border-radius:50%;background:var(--white);color:var(--navy);font-size:13px;line-height:24px}
  .diet{position:absolute;top:332px;left:0;right:0;color:var(--white);font-size:10px;letter-spacing:1.5px;font-weight:500}

  .facts{position:absolute;left:822px;top:14px;width:273px;height:218px;background:var(--white);border:1.5px solid var(--navy);
    padding:5px 8px;color:var(--grey-text);font-size:10.5px;line-height:1.3}
  .facts h3{font-family:"Archivo",Arial,sans-serif;font-weight:800;font-size:19px;color:#111;line-height:1.1}
  .facts .rule-thick{border-top:5px solid #111;margin:3px 0}
  .facts .rule{border-top:1px solid #111;margin:3px 0}
  .facts .row{display:flex;justify-content:space-between}
  .facts .head{justify-content:flex-end;gap:28px}
  .below-facts{position:absolute;left:822px;top:238px;width:273px;color:var(--white);font-size:10.5px;line-height:1.3}
  .below-facts b{font-weight:700}
</style>
</head>
<body>
  <div class="brand-mark"><span class="dot"></span><span class="name">Vellow Naturals</span></div>

  <section class="label" aria-label="Omni Dermal Capsules bottle label">
    <div class="band"></div>

    <div class="info-box usage">
      <h4>SUGGESTED USE:</h4>
      Take three (3) capsules one or more times a day or as directed by your care professional. For best results take on an empty stomach with 8 oz. glass of water.
    </div>
    <div class="info-box caution">
      <h4>CAUTION</h4>
      Do not exceed recommended dose. Pregnant or nursing mothers, children under age of 18 and individuals with a known medical condition should consult a physician before using this or any dietary supplement.
    </div>
    <div class="info-box warning">
      KEEP OUT OF REACH OF CHILDREN.<br>DO NOT USE IF SAFETY SEAL IS DAMAGED OR MISSING. STORE IN A COOL, DRY PLACE
    </div>
    <div class="info-box disclaimer">
      *These statements have not been evaluated by the Food and Drug Administration. This product is not intended to diagnose, treat, cure or prevent diseases.
    </div>
    <p class="lot-note">Lot# and expiration date printed on the bottom of bottle</p>

    <div class="front">
      <div class="mini-brand"><span class="dot"></span><span class="name">Vellow Naturals</span></div>
      <div class="title-box">
        <div class="product">OMNI DERMAL</div>
        <div class="form">CAPSULES</div>
      </div>
      <div class="type-bar">HYDROLYZED TYPE</div>
      <div class="collagen-bar">I, II, III, V &amp; X COLLAGEN</div>
      <ul class="claims">
        <li>SUPPORT JOINTS &amp; BONES</li>
        <li>REJUVENATE SKIN</li>
        <li>PROMOTES HEALTHY HAIR &amp; NAILS</li>
      </ul>
      <div class="count"><span class="num">90</span>CAPSULES</div>
      <div class="diet">DIETARY SUPPLEMENTS</div>
    </div>

    <div class="facts">
      <h3>Supplement Facts</h3>
      <div>Serving size: 3 Capsules</div>
      <div>Servings Per Container: 30</div>
      <div class="rule-thick"></div>
      <div class="row head"><span>Amount Per Serving</span><span>%DV</span></div>
      <div class="rule"></div>
      <div class="row"><span>Premium Collagen&nbsp;&nbsp;&nbsp;&nbsp;1500 mg<br>Protein Complex</span><span>**</span></div>
      <div class="rule"></div>
      <div>Bovine Collagen Peptides, Hydrolyzed, Pure Hydrolyzed Marine Collagen Peptides, Eggshell Membrane Collagen Peptides, Avian Sternum Collagen Peptides</div>
      <div class="rule-thick"></div>
      <div>** Daily Value not established (DV)</div>
    </div>
    <div class="below-facts">
      <b>Inactive ingredient :</b> Gelatin Capsules<br>
      <b>Contains:</b> Egg, Fish<br>
      <b>Contains no added:</b> Milk, Tree Nuts, Wheat, Peanuts, Soy, Shellfish
    </div>
  </section>
</body>
</html>
```